BRIGHT RIVER POWER.

I'd like my business logo.
contact name: Dennis Halvorsen
phone:0438759164
email: info@brightriverpower.net.au
website: www.brightriverpower.net.au

services:
solar
battery storage
LED lighting
energy saving solutions
general electrical
I'd like the design to look professional

Target Market(s)

Everyone

Industry/Entity Type

Business

Contact Information for Business Card

as described above

Requirements
Must have
• Id like the colours and the design to work well with my logo.

```html
<!DOCTYPE html>
<html lang="en">
<head>
<meta charset="utf-8">
<title>Bright River Power – Business Card</title>
<link href="https://fonts.googleapis.com/css2?family=Open+Sans:ital,wght@0,400;0,600;0,700;1,700&display=swap" rel="stylesheet">
<style>
  :root {
    --page-bg: #e9e6df;
    --card-white: #ffffff;
    --brand-green: #5aa52a;
    --panel-light: #8cc63f;
    --panel-dark: #3f9a3a;
    --band-orange: #ef9412;
    --sun-orange: #f6a91b;
    --ink: #3d3d3d;
    --name-tint: #eef6e2;
  }
  * { box-sizing: border-box; margin: 0; padding: 0; }
  html, body {
    width: 1200px; height: 843px; overflow: hidden;
    background: var(--page-bg);
    font-family: "Open Sans", Arial, sans-serif;
  }
  .card {
    position: absolute; left: 100px; top: 121px;
    width: 1000px; height: 600px;
    background: var(--card-white);
    border-radius: 30px;
    overflow: hidden;
    box-shadow: 0 12px 30px rgba(0,0,0,.18);
  }
  .feature-panel {
    position: absolute; left: 540px; top: 130px;
    width: 460px; height: 402px;
    background: linear-gradient(135deg, var(--panel-dark) 0%, var(--panel-light) 100%);
  }
  .brand {
    position: absolute; left: 62px; top: 62px;
    display: flex; align-items: center; gap: 16px;
  }
  .brand-dot {
    width: 46px; height: 46px; border-radius: 50%;
    background: var(--sun-orange);
  }
  .brand-name {
    font-weight: 700; font-size: 38px; letter-spacing: .5px;
    color: var(--brand-green);
  }
  .contacts {
    position: absolute; left: 62px; top: 238px;
    list-style: none;
  }
  .contacts li {
    display: flex; align-items: center; gap: 14px;
    font-size: 21px; color: var(--ink);
    height: 34px;
  }
  .contacts svg { width: 20px; height: 20px; flex: none; }
  .person-name {
    position: absolute; right: 60px; top: 400px;
    font-weight: 700; font-size: 34px;
    color: var(--name-tint);
    text-shadow: 0 1px 2px rgba(0,0,0,.25);
  }
  .services-band {
    position: absolute; left: 0; bottom: 0;
    width: 100%; height: 68px;
    background: var(--band-orange);
    display: flex; align-items: center;
    padding-left: 30px;
    color: #fff; font-style: italic; font-weight: 700; font-size: 22px;
    white-space: nowrap;
  }
  .services-band .sep { margin: 0 10px; font-style: normal; }
</style>
</head>
<body>
  <div class="card">
    <div class="feature-panel" role="img" aria-label="Green leaf illustration area"></div>

    <div class="brand">
      <span class="brand-dot"></span>
      <span class="brand-name">BRIGHT RIVER POWER</span>
    </div>

    <ul class="contacts">
      <li>
        <svg viewBox="0 0 24 24"><path fill="#5aa52a" d="M6.6 10.8a15.1 15.1 0 0 0 6.6 6.6l2.2-2.2c.3-.3.7-.4 1-.2 1.1.4 2.3.6 3.6.6.6 0 1 .4 1 1V20c0 .6-.4 1-1 1A17 17 0 0 1 3 4c0-.6.4-1 1-1h3.5c.6 0 1 .4 1 1 0 1.3.2 2.5.6 3.6.1.3 0 .7-.2 1z"/></svg>
        <span>0438759164</span>
      </li>
      <li>
        <svg viewBox="0 0 24 24"><path fill="#5aa52a" d="M2 5h20v14H2z"/><path d="M2 5l10 8 10-8" fill="none" stroke="#fff" stroke-width="2"/></svg>
        <span>info@brightriverpower.net.au</span>
      </li>
      <li>
        <svg viewBox="0 0 24 24"><circle cx="12" cy="12" r="10" fill="#5aa52a"/><path d="M2 12h20M12 2c3 3 3 17 0 20M12 2c-3 3-3 17 0 20" fill="none" stroke="#fff" stroke-width="1.5"/></svg>
        <span>www.brightriverpower.net.au</span>
      </li>
    </ul>

    <div class="person-name">Dennis Halvorsen</div>

    <div class="services-band">
      Solar<span class="sep">✸</span>Battery storage<span class="sep">✸</span>LED lighting<span class="sep">✸</span>Energy saving solutions<span class="sep">✸</span>General electrical
    </div>
  </div>
</body>
</html>
```